Business card design needed

I run a Beautician studio (for 7 years now)
I offer
- Velmo Body Sugaring
- Ruby Glaze
- Nails
- Facials
- Manicure
- Foot Treatment
It might not be necessary to list all those treatments?
Maybe the link to the Website is sufficient?
I leave that up to you ...
(more info on www.FernAndDewByLenka.com.au)
Velmo BodySugaring is our biggest success, It replaces waxing.
I would like to incorporate the logo into the Business Card.
We had many complaints regarding our old Business Cards as the Phone Number was to small.
On the backside, we would like a "your next Appointment" section.
Looking forward to you Design, cheers ... Lenka
Industry/Entity Type
Business
Contact Information for Business Card
Fern by Dew by Lenka
14 Korrin Sqr 3942 Berwick
www.FernAndDewByLenka.com.au
03 9481 2267

```html
<!DOCTYPE html>
<html lang="en">
<head>
<meta charset="utf-8">
<title>Fern by Dew by Lenka – Business Cards</title>
<link rel="stylesheet" href="https://fonts.googleapis.com/css2?family=Arimo:wght@400;700&family=Cinzel:wght@400&family=Open+Sans:wght@400;600&family=Marcellus&display=swap">
<style>
  :root {
    --backdrop: #3b2c24;
    --card: #ffffff;
    --ink: #2b2b2b;
    --ink-soft: #555555;
    --green: #1f8a3a;
    --rule: #b5b5b5;
    --box-line: #6d6d6d;
    --sun-top: #f7a81b;
    --sun-bottom: #f26522;
    --faint: rgba(31, 138, 58, 0.10);
  }
  * { box-sizing: border-box; margin: 0; padding: 0; }
  html, body { width: 1200px; height: 724px; overflow: hidden; }
  body { background: var(--backdrop); position: relative; font-family: "Open Sans", Arial, sans-serif; color: var(--ink); }

  .card { position: absolute; width: 534px; height: 303px; background: var(--card); border-radius: 22px; overflow: hidden; }
  .card--front   { left: 48px;  top: 39px; }
  .card--appt    { left: 614px; top: 39px; }
  .card--back    { left: 50px;  top: 377px; }
  .card--appt-b  { left: 623px; top: 380px; }

  /* brand name block (stands where the mark sits) */
  .brand { position: absolute; display: flex; align-items: center; gap: 10px; font-family: "Cinzel", Georgia, serif; color: var(--ink); letter-spacing: 2px; }
  .brand__dot { border-radius: 50%; background: linear-gradient(var(--sun-top), var(--sun-bottom)); flex: none; }
  .card--front .brand { left: 34px; top: 62px; font-size: 19px; }
  .card--front .brand__dot { width: 30px; height: 30px; }
  .card--back .brand { left: 0; right: 0; top: 70px; justify-content: center; font-size: 30px; }
  .card--back .brand__dot { width: 48px; height: 48px; }
  .card--appt-b .brand { right: 26px; top: 38px; font-size: 11px; letter-spacing: 1px; gap: 6px; }
  .card--appt-b .brand__dot { width: 18px; height: 18px; }

  .watermark { position: absolute; left: 0; right: 0; top: 118px; text-align: center; font-family: "Cinzel", Georgia, serif; font-size: 40px; letter-spacing: 6px; color: var(--faint); }

  /* front */
  .front__rule { position: absolute; left: 0; right: 0; top: 166px; height: 3px; background: linear-gradient(90deg, #e6e6e6, var(--rule)); }
  .contact { position: absolute; left: 34px; top: 180px; font-family: "Arimo", Arial, sans-serif; }
  .contact__name { font-size: 20px; font-weight: 700; color: var(--ink); }
  .contact__address { font-size: 14px; margin-top: 4px; }
  .contact__line { display: flex; align-items: center; gap: 7px; }
  .contact__phone { font-size: 16px; margin-top: 16px; }
  .contact__web { font-size: 14px; margin-top: 8px; }
  .contact svg { flex: none; }
  .treatments { position: absolute; right: 20px; top: 180px; text-align: right; font-family: "Arimo", Arial, sans-serif; font-size: 14px; line-height: 21px; }
  .treatments__title { color: var(--green); font-weight: 700; font-size: 17px; letter-spacing: 1px; margin-bottom: 2px; }

  /* back */
  .back__web { position: absolute; left: 0; right: 0; top: 200px; text-align: center; font-size: 14px; letter-spacing: 2.6px; }
  .back__hours-title { position: absolute; left: 0; right: 0; top: 232px; text-align: center; font-size: 19px; font-weight: 600; letter-spacing: 1.6px; color: var(--ink-soft); }
  .back__hours { position: absolute; left: 0; right: 0; top: 267px; text-align: center; font-size: 14.5px; font-weight: 600; color: var(--ink-soft); }
  .back__hours .sep { color: #aaa; margin: 0 7px; font-weight: 400; }

  /* appointment */
  .appt { position: absolute; left: 36px; top: 52px; right: 30px; color: var(--ink-soft); font-size: 14.5px; }
  .appt__title { font-family: "Marcellus", Georgia, serif; color: var(--green); font-size: 17px; letter-spacing: 0.5px; }
  .appt__row { display: flex; align-items: flex-end; height: 38px; }
  .appt__fill { border-bottom: 1px dotted var(--box-line); height: 1px; margin: 0 6px 6px; }
  .appt__fill--solid { border-bottom-style: solid; }
  .appt__box { width: 96px; height: 21px; border: 1px solid var(--box-line); margin-right: 32px; }
  .appt__box:first-of-type { margin-left: 10px; }
  .appt__days { display: flex; align-items: center; gap: 8px; margin-top: 12px; font-weight: 600; font-size: 14px; }
  .appt__day-box { width: 33px; height: 20px; border: 1px solid var(--box-line); margin-right: 4px; }
  .appt__note { margin-top: 18px; font-size: 12.5px; line-height: 18px; color: var(--ink); }
</style>
</head>
<body>

<section class="card card--front" aria-label="Business card front">
  <div class="brand"><span class="brand__dot"></span>Velmo Body Sugaring</div>
  <div class="front__rule"></div>
  <div class="contact">
    <p class="contact__name">Fern by Dew by Lenka</p>
    <p class="contact__address">14 Korrin Sqr 3942 Berwick</p>
    <p class="contact__line contact__phone">
      <svg width="14" height="14" viewBox="0 0 24 24"><circle cx="12" cy="12" r="11" fill="none" stroke="#1f8a3a" stroke-width="2"/><path d="M8 6l2 3-1.5 1.5a8 8 0 0 0 5 5L15 14l3 2-1 2.5c-5 0-10-5-10-10z" fill="#1f8a3a"/></svg>
      03 9481 2267
    </p>
    <p class="contact__line contact__web">
      <svg width="13" height="13" viewBox="0 0 24 24" fill="none" stroke="#1f8a3a" stroke-width="2"><circle cx="12" cy="12" r="10"/><path d="M2 12h20M12 2c3 3 3 17 0 20M12 2c-3 3-3 17 0 20"/></svg>
      www.FernAndDewByLenka.com.au
    </p>
  </div>
  <div class="treatments">
    <p class="treatments__title">Treatments offer</p>
    <p>• Velmo Body Sugaring</p>
    <p>• Ruby Glaze • Nails</p>
    <p>• Facials • Manicure</p>
    <p>• Foot Treatment</p>
  </div>
</section>

<section class="card card--appt" aria-label="Appointment card">
  <div class="watermark" aria-hidden="true">VELMO</div>
  <div class="appt">
    <p class="appt__title">YOUR APPOINTMENT</p>
    <div class="appt__row" style="height:30px">Name :<span class="appt__fill" style="width:290px"></span></div>
    <div class="appt__row">Date :<span class="appt__fill appt__fill--solid" style="width:96px;margin-left:16px"></span>Time :<span class="appt__fill appt__fill--solid" style="width:90px;margin-right:2px"></span>am / pm</div>
    <div class="appt__row">Next Appointment<span class="appt__box"></span><span class="appt__box"></span></div>
    <div class="appt__days">MON<span class="appt__day-box"></span>TUE<span class="appt__day-box"></span>WED<span class="appt__day-box"></span>THU<span class="appt__day-box"></span>FRI<span class="appt__day-box"></span>SAT<span class="appt__day-box"></span></div>
    <p class="appt__note">It would be appreciated if 24 hours notice could be given if you are unable to attend an appointment</p>
  </div>
</section>

<section class="card card--back" aria-label="Business card back">
  <div class="brand"><span class="brand__dot"></span>Velmo Body Sugaring</div>
  <p class="back__web">www.FernAndDewByLenka.com.au</p>
  <p class="back__hours-title">Hours of Operation</p>
  <p class="back__hours">Mon - Fri: 7.30am - 7.00pm<span class="sep">|</span>Saturday: 7.30am - 12.00pm</p>
</section>

<section class="card card--appt-b" aria-label="Appointment card with brand name">
  <div class="brand"><span class="brand__dot"></span>Velmo Body Sugaring</div>
  <div class="appt" style="top:55px">
    <p class="appt__title">YOUR APPOINTMENT</p>
    <div class="appt__row" style="height:30px">Name :<span class="appt__fill" style="width:290px"></span></div>
    <div class="appt__row">Date :<span class="appt__fill appt__fill--solid" style="width:96px;margin-left:16px"></span>Time :<span class="appt__fill appt__fill--solid" style="width:90px;margin-right:2px"></span>am / pm</div>
    <div class="appt__row">Next Appointment<span class="appt__box"></span><span class="appt__box"></span></div>
    <div class="appt__days">MON<span class="appt__day-box"></span>TUE<span class="appt__day-box"></span>WED<span class="appt__day-box"></span>THU<span class="appt__day-box"></span>FRI<span class="appt__day-box"></span>SAT<span class="appt__day-box"></span></div>
    <p class="appt__note">It would be appreciated if 24 hours notice could be given if you are unable to attend an appointment</p>
  </div>
</section>

</body>
</html>
```